Modern Verdell Tree Care Website

I need a website for a full service Tree Care company. The company provides tree pruning, tree removal, tree preservation, emergency services, stump grinding, and emergency tree services.

Target Market(s)

Customers that need tree services

Industry/Entity Type

Landscaping, Tree Services

Coding

Coded - Design and coding required

Number of Pages Required

5+ page

Font styles to use
Sans Serif

Requirements
Must have
• Good clean design that showcases the services the company provides.
Nice to have
• Services page; contact form, blog, home page, about page

```html
<!DOCTYPE html>
<html lang="en">
<head>
<meta charset="utf-8">
<title>Verdell Tree Care</title>
<link href="https://fonts.googleapis.com/css2?family=Open+Sans:wght@400;600;700;800&family=Poppins:wght@400;500;600&display=swap" rel="stylesheet">
<style>
:root{
  --green:#7cc243;
  --green-dark:#5fa22c;
  --orange:#f7a532;
  --navy:#151a3d;
  --blue:#1f2a8c;
  --ink:#1b1e2e;
  --muted:#6b6f80;
  --topbar:#5b6770;
  --light:#f5f5f6;
  --footer:#0e1328;
  --footer-card:#1a1f38;
  --white:#fff;
}
*{margin:0;padding:0;box-sizing:border-box}
html,body{width:1200px;height:4598px;overflow:hidden}
body{position:relative;background:var(--white);font-family:"Open Sans",sans-serif;color:var(--ink)}
.abs{position:absolute}
.photo{position:absolute}
a{color:inherit;text-decoration:none}

/* top bar + header */
.topbar{left:0;top:0;width:1200px;height:29px;background:var(--topbar);color:#fff;font:400 11px "Poppins",sans-serif;display:flex;align-items:center;justify-content:center;gap:6px}
.header{left:0;top:29px;width:1200px;height:114px;background:#fff}
.brand{left:125px;top:64px;display:flex;align-items:center;gap:12px}
.brand-mark{width:48px;height:48px;background:var(--green)}
.brand-name{font:700 26px "Open Sans",sans-serif;color:var(--topbar);line-height:1;letter-spacing:.5px}
.phone{left:689px;top:56px;font:400 16px "Poppins",sans-serif;color:var(--navy);display:flex;align-items:center;gap:8px}
.btn-appt{left:857px;top:46px;width:193px;height:40px;background:var(--green);color:#fff;font:600 12px "Poppins",sans-serif;display:flex;align-items:center;justify-content:center;letter-spacing:.3px}
.nav{left:0;top:105px;font:500 12px "Poppins",sans-serif;color:var(--navy)}
.nav a{position:absolute;white-space:nowrap}
.nav a.active{color:var(--green)}
.nav a.active::after{content:"";position:absolute;left:-4px;right:-4px;top:28px;height:3px;background:var(--green)}

/* hero */
.hero-bg{left:0;top:143px;width:1200px;height:777px;background:linear-gradient(120deg,#2d3a24 0%,#4b5a34 40%,#3a4528 70%,#5a5f45 100%)}
.hero-bg::after{content:"";position:absolute;inset:0;background:rgba(20,28,16,.35)}
.hero-tag{left:95px;top:307px;width:267px;height:45px;background:rgba(110,120,130,.75);border-left:4px solid var(--green);color:#fff;font:700 20px "Open Sans",sans-serif;display:flex;align-items:center;padding-left:20px}
.hero-title{left:95px;top:380px;color:#fff;font:700 50px "Open Sans",sans-serif}
.hero-text{left:95px;top:470px;width:450px;color:#fff;font:400 16px/1.7 "Open Sans",sans-serif}
.btn-read{left:95px;top:550px;width:175px;height:50px;background:var(--green);color:#fff;font:700 16px "Open Sans",sans-serif;display:flex;align-items:center;justify-content:center}
.hero-portrait{left:646px;top:175px;width:411px;height:489px;border-radius:150px 0 90px 0;background:linear-gradient(180deg,#c9b8a0 0%,#b6c0c8 35%,#5d7fa8 70%,#43618a 100%)}
.hero-wave{left:0;top:760px;width:1200px;height:162px}

/* about */
.eyebrow{font:500 11px "Poppins",sans-serif;color:var(--green);letter-spacing:.3px;text-transform:uppercase}
.eyebrow.line{border-bottom:1px solid var(--green);padding-bottom:4px}
.about-eyebrow{left:125px;top:990px}
.about-title{left:125px;top:1025px;font:700 38px/1.25 "Open Sans",sans-serif;color:var(--navy)}
.about-sub{left:125px;top:1144px;font:400 19px "Open Sans",sans-serif;color:var(--ink)}
.about-text{left:125px;width:465px;font:400 12px/1.6 "Open Sans",sans-serif;color:var(--muted)}
.btn-contact{left:129px;top:1320px;width:155px;height:44px;background:var(--green);color:#fff;font:700 15px "Open Sans",sans-serif;display:flex;align-items:center;justify-content:center;gap:14px}
.about-badge{left:637px;top:912px;width:440px;height:460px}

/* services */
.services{left:0;top:1429px;width:1200px;height:643px;background:var(--light)}
.services-eyebrow{left:0;top:1488px;width:1200px;text-align:center}
.services-eyebrow span{border-bottom:1px solid var(--green);padding-bottom:4px}
.services-title{left:0;top:1522px;width:1200px;text-align:center;font:700 42px "Open Sans",sans-serif;color:var(--navy)}
.card{top:1620px;width:305px;height:364px;border-radius:24px;overflow:hidden}
.card-label{position:absolute;left:44px;top:205px;font:400 11px "Poppins",sans-serif;color:#fff;z-index:1}
.card-title{position:absolute;left:30px;top:230px;font:700 19px "Open Sans",sans-serif;color:#fff;z-index:1}
.card-arrow{position:absolute;left:30px;top:300px;width:36px;height:36px;border-radius:50%;background:#fff;display:flex;align-items:center;justify-content:center;z-index:1}
.card::before{content:"";position:absolute;inset:0;background:linear-gradient(180deg,rgba(0,0,0,0) 45%,rgba(0,0,0,.5) 100%)}

/* why choose */
.why-bg{left:0;top:2090px;width:1200px;height:690px;z-index:2}
.why-text{z-index:3}
.why-eyebrow{left:670px;top:2244px;color:#fff}
.why-title{left:670px;top:2275px;font:700 38px/1.3 "Open Sans",sans-serif;color:#fff}
.feature{left:664px;display:flex;align-items:center;gap:14px}
.feature-icon{width:64px;height:64px;border-radius:50%;background:#fff;display:flex;align-items:center;justify-content:center}
.feature h3{font:700 18px "Open Sans",sans-serif;color:#fff}
.feature p{font:400 12px "Open Sans",sans-serif;color:#e8e8e8;margin-top:3px}

/* faq */
.faq-bg{left:0;top:2700px;width:1200px;height:729px;background:#eff0f3}
.faq-photo{left:540px;top:2700px;width:660px;height:729px;background:linear-gradient(90deg,rgba(239,240,243,1) 0%,rgba(150,150,130,.8) 14%,#6f7a45 40%,#8a8a60 60%,#6b6a4a 80%,#5e5a3f 100%)}
.faq-eyebrow{left:148px;top:2878px;display:flex;align-items:center;gap:10px;font:600 13px "Poppins",sans-serif;color:var(--blue)}
.faq-eyebrow i{display:block;width:52px;height:1px;background:var(--green)}
.faq-title{left:148px;top:2905px;font:700 37px "Open Sans",sans-serif;color:var(--blue)}
.faq-item{left:132px;width:500px;background:#fff;box-shadow:0 2px 10px rgba(0,0,0,.05)}
.faq-q{height:56px;display:flex;align-items:center;justify-content:space-between;padding:0 26px;font:600 14px "Open Sans",sans-serif;color:var(--blue)}
.faq-toggle{width:24px;height:24px;border-radius:50%;background:var(--green);display:flex;align-items:center;justify-content:center}
.faq-a{margin:0 26px;background:#f2f3f5;padding:18px 24px;font:400 14px/1.65 "Open Sans",sans-serif;color:var(--muted)}

/* testimonials */
.t-eyebrow{left:174px;top:3558px;font:500 17px "Poppins",sans-serif;color:var(--green)}
.t-title{left:174px;top:3590px;font:700 34px/1.3 "Open Sans",sans-serif;color:var(--navy)}
.t-text{left:174px;top:3688px;width:405px;font:400 12px/1.9 "Open Sans",sans-serif;color:var(--muted)}
.t-author{left:174px;top:3790px;display:flex;align-items:center;gap:14px}
.avatar{border-radius:50%;background:linear-gradient(160deg,#c7cbd3,#7f8591);border:4px solid #fff;box-shadow:0 3px 10px rgba(0,0,0,.15)}
.t-author h4{font:700 16px "Open Sans",sans-serif;color:var(--ink)}
.t-author p{font:400 11px "Open Sans",sans-serif;color:var(--muted)}
.t-arrows{left:174px;top:3872px;display:flex;gap:18px}
.t-circle{left:644px;top:3545px;width:376px;height:376px}

/* footer */
.footer-wave{left:0;top:4000px;width:1200px;height:170px}
.footer{left:0;top:4160px;width:1200px;height:438px;background:var(--footer)}
.footer-card{left:59px;top:4242px;width:343px;height:268px;border-radius:18px;background:var(--footer-card);padding:34px 26px}
.footer-brand{display:flex;align-items:center;gap:10px;font:700 22px "Open Sans",sans-serif;color:#fff}
.footer-brand i{display:block;width:34px;height:34px;background:#fff}
.footer-card p{margin-top:22px;font:400 14px/1.6 "Open Sans",sans-serif;color:#fff}
.socials{display:flex;gap:10px;margin-top:20px}
.socials span{width:34px;height:34px;border-radius:50%;background:#1b74e4}
.f-col{top:4240px;color:#fff}
.f-col h5{font:600 15px "Open Sans",sans-serif;margin-bottom:20px}
.f-col li{list-style:none;font:400 14px "Open Sans",sans-serif;height:35px}
.f-loc p{font:400 14px/1.6 "Open Sans",sans-serif;width:340px}
.f-loc .row{display:flex;align-items:center;gap:10px;font:400 12px "Open Sans",sans-serif;margin-top:12px}
.f-rule{left:414px;top:4540px;width:786px;height:1px;background:#3a3f58}
.f-legal{left:920px;top:4566px;display:flex;gap:22px;font:400 12px "Open Sans",sans-serif;color:#fff}
.to-top{left:1153px;top:4565px;width:32px;height:33px;background:var(--green);display:flex;align-items:center;justify-content:center}
</style>
</head>
<body>

<!-- top bar -->
<div class="abs topbar">
  <svg width="10" height="13" viewBox="0 0 10 13"><path d="M5 1a4 4 0 0 0-4 4c0 3 4 7 4 7s4-4 4-7a4 4 0 0 0-4-4z" fill="none" stroke="#fff" stroke-width="1.2"/><circle cx="5" cy="5" r="1.4" fill="#fff"/></svg>
  Suite 4, Elmstead Road
</div>

<!-- header -->
<header class="abs header"></header>
<div class="abs brand"><span class="brand-mark"></span><span class="brand-name">Verdell Tree Care</span></div>
<div class="abs phone">
  <svg width="16" height="16" viewBox="0 0 16 16"><path d="M3 1.5l2.5 0 1.2 3-1.6 1.2c.8 1.8 2.3 3.3 4.1 4.1l1.2-1.6 3 1.2v2.5c0 .8-.7 1.5-1.5 1.5C6.7 13.4 2.6 9.3 1.5 3 1.5 2.2 2.2 1.5 3 1.5z" fill="var(--green)"/></svg>
  (000) 555-0142
</div>
<a class="abs btn-appt" href="#">REQUEST APPOINTMENT</a>
<nav class="abs nav">
  <a class="active" style="left:421px" href="#">HOME</a>
  <a style="left:494px" href="#">ABOUT US</a>
  <a style="left:596px" href="#">SERVICES</a>
  <a style="left:700px" href="#">PROJECTS</a>
  <a style="left:805px" href="#">CONTACT US</a>
</nav>

<!-- hero -->
<div class="photo hero-bg" role="img" aria-label="Photo of a tree trunk and forest canopy in deep green tones"></div>
<div class="abs hero-tag">Experts in</div>
<h1 class="abs hero-title">Tree Care</h1>
<p class="abs hero-text">Lorem ipsum dolor sit amet, consectetur adipiscing elit, sed do eiusmod tempor incidi</p>
<a class="abs btn-read" href="#">Read More</a>
<div class="photo hero-portrait" role="img" aria-label="Photo of a smiling arborist in a hard hat and safety vest by the sea"></div>
<svg class="abs hero-wave" viewBox="0 0 1200 162" preserveAspectRatio="none">
  <path d="M0 60 C120 120 380 130 620 90 C820 55 1000 15 1200 8 L1200 162 L0 162Z" fill="var(--orange)"/>
  <path d="M0 95 C150 150 420 150 660 110 C850 75 1000 35 1200 20 L1200 162 L0 162Z" fill="var(--green)"/>
  <path d="M0 140 C180 165 460 140 700 100 C880 70 1040 30 1200 22 L1200 162 L0 162Z" fill="#fff"/>
</svg>

<!-- about -->
<div class="abs eyebrow line about-eyebrow">Who we are</div>
<h2 class="abs about-title">We Offer Sustainable<br>Tree Solutions</h2>
<p class="abs about-sub">Enhancing Landscapes, One Tree at a Time</p>
<p class="abs about-text" style="top:1185px">Lorem ipsum dolor sit amet, consectetur adipiscing elit, sed do eiusmod temp or incididunt ut labore et dolore magna aliqua. Ut enim ad minim veniam, quis laboris nisi ut aliquip ex ea commodo consequat.</p>
<p class="abs about-text" style="top:1255px">Lorem ipsum dolor sit amet, consectetur adipiscing elit, sed do eiusmod temp or incididunt ut labore et dolore magna aliqua.</p>
<a class="abs btn-contact" href="#">Contact us
  <svg width="18" height="12" viewBox="0 0 18 12"><path d="M1 6h15M11 1l5 5-5 5" fill="none" stroke="#fff" stroke-width="1.6"/></svg>
</a>
<svg class="abs about-badge" viewBox="0 0 440 460">
  <defs>
    <path id="arcText" d="M16 250 A204 204 0 0 1 424 250"/>
    <linearGradient id="climbGrad" x1="0" y1="0" x2="0" y2="1"><stop offset="0" stop-color="#c6ccd0"/><stop offset=".5" stop-color="#8f979b"/><stop offset="1" stop-color="#6f7468"/></linearGradient>
  </defs>
  <text font-family="Open Sans, sans-serif" font-size="17" fill="var(--navy)" letter-spacing="1"><textPath href="#arcText" startOffset="3%">YOUR PROFESSIONAL EXPERTS IN THE AREA</textPath></text>
  <path d="M41.5 315 A190 190 0 1 0 384.5 155" fill="none" stroke="#8a88c4" stroke-width="3"/>
  <circle cx="220" cy="250" r="175" fill="url(#climbGrad)" role="img" aria-label="Photo of an arborist in blue climbing gear high in a bare tree"/>
</svg>

<!-- services -->
<section class="abs services"></section>
<div class="abs eyebrow services-eyebrow"><span>Our services</span></div>
<h2 class="abs services-title">Services We Provide</h2>
<div class="abs card" style="left:116px;background:linear-gradient(160deg,#6d9a3a,#3e6a2a 50%,#8a8c84)" role="img" aria-label="Photo of a worker pruning branches with long loppers">
  <span class="card-label">Our Services</span><span class="card-title">Tree Pruning</span>
  <span class="card-arrow"><svg width="14" height="12" viewBox="0 0 14 12"><path d="M1 6h11M8 2l4 4-4 4" fill="none" stroke="var(--navy)" stroke-width="1.5"/></svg></span>
</div>
<div class="abs card" style="left:445px;background:linear-gradient(170deg,#7b8a3a,#b49b5a 40%,#7ea23a 75%,#5b8a2a)" role="img" aria-label="Photo of a felled log lying on grass">
  <span class="card-label">Our Services</span><span class="card-title">Tree Removal</span>
  <span class="card-arrow"><svg width="14" height="12" viewBox="0 0 14 12"><path d="M1 6h11M8 2l4 4-4 4" fill="none" stroke="var(--navy)" stroke-width="1.5"/></svg></span>
</div>
<div class="abs card" style="left:772px;background:linear-gradient(160deg,#4b7a33,#5d8a3e 45%,#3f4a52)" role="img" aria-label="Photo of two gardeners working beside a row of hedges">
  <span class="card-label">Our Services</span><span class="card-title">Stump Grinding</span>
  <span class="card-arrow"><svg width="14" height="12" viewBox="0 0 14 12"><path d="M1 6h11M8 2l4 4-4 4" fill="none" stroke="var(--navy)" stroke-width="1.5"/></svg></span>
</div>

<!-- faq (sits beneath the why-choose wave) -->
<div class="abs faq-bg"></div>
<div class="photo faq-photo" role="img" aria-label="Photo of a worker in an orange helmet cutting a stump with a chainsaw"></div>
<div class="abs faq-eyebrow"><i></i>FAQS</div>
<h2 class="abs faq-title">Know Before You Start</h2>
<div class="abs faq-item" style="top:2983px;height:189px">
  <div class="faq-q">How Do I Get Regular Service Started?
    <span class="faq-toggle"><svg width="10" height="7" viewBox="0 0 10 7"><path d="M1 6l4-4 4 4" fill="none" stroke="#fff" stroke-width="1.6"/></svg></span>
  </div>
  <div class="faq-a">Lorem ipsum dolor sit amet, consectetur adipiscing elit, sed do eiusmod tempor incididunt Lorem ipsum dolor sit amet, consectetur adipiscing.</div>
</div>
<div class="abs faq-item" style="top:3184px"><div class="faq-q">How Do I Get Regular Service Started?<svg width="10" height="6" viewBox="0 0 10 6"><path d="M1 1l4 4 4-4" fill="var(--muted)"/></svg></div></div>
<div class="abs faq-item" style="top:3252px"><div class="faq-q">How Do I Get Regular Service Started?<svg width="10" height="6" viewBox="0 0 10 6"><path d="M1 1l4 4 4-4" fill="var(--muted)"/></svg></div></div>
<div class="abs faq-item" style="top:3320px"><div class="faq-q">How Do I Get Regular Service Started?<svg width="10" height="6" viewBox="0 0 10 6"><path d="M1 1l4 4 4-4" fill="var(--muted)"/></svg></div></div>

<!-- why choose us -->
<svg class="abs why-bg" viewBox="0 0 1200 690" preserveAspectRatio="none" role="img" aria-label="Photo of a sunny park with large trees fading into a dark backdrop">
  <defs>
    <linearGradient id="whyGrad" x1="0" y1="0" x2="1" y2="0">
      <stop offset="0" stop-color="#4f7a2c"/>
      <stop offset=".3" stop-color="#6e9a3a"/>
      <stop offset=".5" stop-color="#2e3a22"/>
      <stop offset=".62" stop-color="#000"/>
      <stop offset="1" stop-color="#000"/>
    </linearGradient>
  </defs>
  <path d="M0 142 C300 40 650 0 900 5 C1050 10 1150 25 1200 40 L1200 600 C1000 680 700 690 450 680 C250 670 100 640 0 620Z" fill="url(#whyGrad)"/>
</svg>
<div class="abs eyebrow why-eyebrow why-text">Why choose us</div>
<h2 class="abs why-title why-text">Your Partner in Tree<br>Presevation</h2>
<div class="abs feature why-text" style="top:2384px">
  <span class="feature-icon"><svg width="26" height="26" viewBox="0 0 26 26"><path d="M5 21h16M8 21l3-9 4 3 3-9" fill="none" stroke="var(--green)" stroke-width="1.6"/><circle cx="18" cy="5" r="2" fill="none" stroke="var(--green)" stroke-width="1.6"/></svg></span>
  <div><h3>On-Time Appointments</h3><p>Inventore veritasis uasvitae dicta suntetur sipid</p></div>
</div>
<div class="abs feature why-text" style="top:2465px">
  <span class="feature-icon"><svg width="26" height="26" viewBox="0 0 26 26"><path d="M5 15v-2a8 8 0 0 1 16 0v2M5 15h3v6H5zM18 15h3v6h-3z" fill="none" stroke="var(--green)" stroke-width="1.6"/></svg></span>
  <div><h3>Qualified Experts</h3><p>Inventore veritasis uasvitae dicta suntetur sipid</p></div>
</div>
<div class="abs feature why-text" style="top:2547px">
  <span class="feature-icon"><svg width="26" height="26" viewBox="0 0 26 26"><path d="M13 3l3 6.5 7 .8-5.2 4.8 1.4 7L13 18.6 6.8 22l1.4-7L3 10.3l7-.8z" fill="none" stroke="var(--green)" stroke-width="1.6"/></svg></span>
  <div><h3>Proven Record</h3><p>Inventore veritasis uasvitae dicta suntetur sipid</p></div>
</div>

<!-- testimonials -->
<div class="abs t-eyebrow">Testimonials</div>
<h2 class="abs t-title">What Our Satisfied<br>Clients are Saying!</h2>
<p class="abs t-text">Lorem ipsum dolor sit amet, consectetur adipiscing elit, sed do eiusmod tempor incididunt ut labore et dolore magna aliqua. Ut enim ad minim veniam, quis nostrud exercitation ullamco la boris nisi ut aliquip ex ea</p>
<div class="abs t-author">
  <span class="avatar" role="img" aria-label="Client portrait" style="width:44px;height:44px;border-width:2px"></span>
  <div><h4>Marcus Hale</h4><p>Client</p></div>
</div>
<div class="abs t-arrows">
  <svg width="26" height="16" viewBox="0 0 26 16"><path d="M25 8H3M9 2L2 8l7 6" fill="none" stroke="var(--ink)" stroke-width="2"/></svg>
  <svg width="26" height="16" viewBox="0 0 26 16"><path d="M1 8h22M17 2l7 6-7 6" fill="none" stroke="var(--ink)" stroke-width="2"/></svg>
</div>
<svg class="abs t-circle" viewBox="0 0 376 376">
  <circle cx="188" cy="188" r="188" fill="#f4f4f5"/>
  <circle cx="188" cy="188" r="134" fill="#e8e8ea"/>
  <circle cx="188" cy="188" r="82" fill="#fff"/>
  <path d="M112 200 A78 78 0 0 0 264 200" fill="none" stroke="var(--green)" stroke-width="4"/>
  <path d="M160 175h22v20c0 14-6 22-18 25l-3-7c6-2 9-6 9-12h-10zM196 175h22v20c0 14-6 22-18 25l-3-7c6-2 9-6 9-12h-10z" fill="var(--navy)"/>
</svg>
<span class="abs avatar" role="img" aria-label="Client portrait" style="left:880px;top:3550px;width:62px;height:62px"></span>
<span class="abs avatar" role="img" aria-label="Client portrait" style="left:668px;top:3645px;width:72px;height:72px"></span>
<span class="abs avatar" role="img" aria-label="Client portrait" style="left:910px;top:3820px;width:80px;height:80px"></span>
<span class="abs avatar" role="img" aria-label="Client portrait" style="left:688px;top:3840px;width:66px;height:66px"></span>

<!-- footer -->
<svg class="abs footer-wave" viewBox="0 0 1200 170" preserveAspectRatio="none">
  <path d="M0 90 C200 30 450 10 700 30 C900 45 1050 80 1200 110 L1200 170 L0 170Z" fill="var(--green)"/>
  <path d="M0 120 C200 60 450 40 700 60 C900 75 1050 110 1200 135 L1200 170 L0 170Z" fill="var(--orange)"/>
  <path d="M0 150 C200 85 450 65 700 85 C900 100 1060 140 1200 160 L1200 170 L0 170Z" fill="var(--footer)"/>
</svg>
<footer class="abs footer"></footer>
<div class="abs footer-card">
  <div class="footer-brand"><i></i>Verdell Tree Care</div>
  <p>Lorem ipsum dolor sit amet, consectetur adipiscing elit, sed do eiusmod tempor in cididunt ut labore et dolore magna aliqua. Ut enim ad minim veniam</p>
  <div class="socials"><span></span><span></span><span></span><span></span></div>
</div>
<div class="abs f-col" style="left:427px"><h5>Quick Links</h5><ul><li>About us</li><li>Careers</li><li>News &amp; Articles</li><li>Legal Notice</li><li>Credits</li></ul></div>
<div class="abs f-col" style="left:611px"><h5>Othe Pages</h5><ul><li>Help Center</li><li>Contact Us</li><li>FAQ</li><li>Community</li><li>Projects</li></ul></div>
<div class="abs f-col f-loc" style="left:796px">
  <h5>Location Address</h5>
  <p>Know where to find us? Let's take a look and get in touch</p>
  <div class="row" style="margin-top:18px"><svg width="12" height="14" viewBox="0 0 12 14"><path d="M6 1a4.5 4.5 0 0 0-4.5 4.5C1.5 9 6 13 6 13s4.5-4 4.5-7.5A4.5 4.5 0 0 0 6 1z" fill="none" stroke="#fff"/><circle cx="6" cy="5.5" r="1.5" fill="#fff"/></svg>18 Birchwood Lane, Ohio</div>
  <div class="row"><svg width="12" height="12" viewBox="0 0 16 16"><path d="M3 1.5h2.5l1.2 3-1.6 1.2c.8 1.8 2.3 3.3 4.1 4.1l1.2-1.6 3 1.2v2.5c0 .8-.7 1.5-1.5 1.5C6.7 13.4 2.6 9.3 1.5 3 1.5 2.2 2.2 1.5 3 1.5z" fill="none" stroke="#fff"/></svg>+000 555 0198</div>
  <div class="row"><svg width="13" height="10" viewBox="0 0 13 10"><rect x=".5" y=".5" width="12" height="9" fill="none" stroke="#fff"/><path d="M.5 .5l6 5 6-5" fill="none" stroke="#fff"/></svg>hello@verdelltrees.com</div>
</div>
<div class="abs f-rule"></div>
<div class="abs f-legal"><span>Privacy Policy</span><span>Terms &amp; Conditions</span></div>
<div class="abs to-top"><svg width="12" height="14" viewBox="0 0 12 14"><path d="M6 13V2M1 7l5-5 5 5" fill="none" stroke="#fff" stroke-width="1.6"/></svg></div>

</body>
</html>
```